Design NEW business card

We would like a business card using the colour deep red wine or dark navy blue textured background (patterned or not, open to suggestions) with a high gloss debossed rose gold/copper RM Roland Mercer Jewellery business name (Provided). I have included images for your review we would like to keep our currently logo and business name on the front but you can change the layout and positioning. For the back of the card we are open to all suggestions/variations.
Business
Use our current RM Roland Mercer Jewellery logo (Provided image)

```html
<!DOCTYPE html>
<html lang="en">
<head>
<meta charset="utf-8">
<title>Roland Mercer Jewellery – Business Card</title>
<link rel="stylesheet" href="https://fonts.googleapis.com/css2?family=Open+Sans:wght@400;600&display=swap">
<style>
  :root {
    --backdrop: #3a322e;
    --card-deep: #0f1320;
    --card-mid: #161b2b;
    --card-edge: #222838;
    --silver: #b9b9b9;
    --silver-dim: #8e8e8e;
    --copper: #c08a64;
    --white: #f2f2f2;
  }
  * { margin: 0; padding: 0; box-sizing: border-box; }
  html, body {
    width: 1200px; height: 864px; overflow: hidden;
    background: var(--backdrop);
    font-family: "Open Sans", Arial, sans-serif;
  }
  .canvas { position: relative; width: 1200px; height: 864px; }
  .card {
    position: absolute; left: 320px; width: 560px; height: 320px;
    background:
      repeating-linear-gradient(45deg, rgba(255,255,255,.018) 0 2px, transparent 2px 5px),
      repeating-linear-gradient(-45deg, rgba(0,0,0,.12) 0 2px, transparent 2px 5px),
      radial-gradient(ellipse at 35% 30%, var(--card-mid), var(--card-deep) 75%);
    border: 1px solid var(--card-edge);
    box-shadow: 0 12px 30px rgba(0,0,0,.45);
  }
  .card--front { top: 60px; }
  .card--back { top: 464px; }

  /* brand lockup: plain circle + name set in text font */
  .brand { position: absolute; text-align: center; font-weight: 400; text-transform: uppercase; }
  .brand-mark {
    display: flex; align-items: center; justify-content: center;
    margin: 0 auto 10px; border-radius: 50%; border: 1px solid currentColor;
    letter-spacing: 2px;
  }
  .brand-name { display: block; letter-spacing: 5px; line-height: 1.2; }
  .brand-sub { display: block; letter-spacing: 9px; margin-top: 4px; }

  /* front */
  .front-brand { left: 90px; top: 50px; width: 260px; color: var(--silver); }
  .front-brand .brand-mark { width: 62px; height: 62px; font-size: 20px; }
  .front-brand .brand-name { font-size: 22px; }
  .front-brand .brand-sub { font-size: 11px; }
  .front-web {
    position: absolute; left: 64px; top: 228px;
    color: var(--silver-dim); font-size: 14px; letter-spacing: 4px;
  }

  /* back */
  .person { position: absolute; left: 30px; top: 66px; }
  .person-name { color: var(--copper); font-weight: 600; font-size: 15px; letter-spacing: .5px; }
  .person-role { color: var(--white); font-size: 12px; margin-top: 1px; }
  .contacts { position: absolute; left: 30px; top: 116px; list-style: none; }
  .contacts li {
    display: flex; align-items: center; gap: 8px;
    color: var(--white); font-size: 12.5px; line-height: 19px;
  }
  .contacts svg { width: 11px; height: 11px; fill: var(--copper); flex: none; }
  .divider {
    position: absolute; left: 30px; right: 26px; top: 204px;
    height: 1px; background: var(--white); opacity: .85;
  }
  .back-brand { right: 34px; top: 40px; width: 230px; color: var(--copper); }
  .back-brand .brand-mark { width: 56px; height: 56px; font-size: 18px; }
  .back-brand .brand-name { font-size: 19px; }
  .back-brand .brand-sub { font-size: 10px; }
  .address {
    position: absolute; right: 30px; top: 224px;
    text-align: right; color: var(--white);
    font-size: 14px; line-height: 20px;
  }
  .address .web { letter-spacing: 1.5px; }
</style>
</head>
<body>
<main class="canvas">
  <section class="card card--front" aria-label="Card front">
    <div class="brand front-brand">
      <span class="brand-mark">RM</span>
      <span class="brand-name">Roland Mercer</span>
      <span class="brand-sub">Jewellery</span>
    </div>
    <p class="front-web">www.mercerfine.com</p>
  </section>

  <section class="card card--back" aria-label="Card back">
    <div class="person">
      <p class="person-name">ELLIS HART</p>
      <p class="person-role">CEO/FOUNDER</p>
    </div>
    <ul class="contacts">
      <li><svg viewBox="0 0 12 12" aria-hidden="true"><path d="M2 1h3l1 3-2 1a7 7 0 0 0 3 3l1-2 3 1v3c0 1-1 1-1 1C5 11 1 7 1 2c0 0 0-1 1-1z"/></svg>555 210 4418</li>
      <li><svg viewBox="0 0 12 12" aria-hidden="true"><path d="M3 0h6a1 1 0 0 1 1 1v10a1 1 0 0 1-1 1H3a1 1 0 0 1-1-1V1a1 1 0 0 1 1-1zm0 2v7h6V2z"/></svg>555 318 2207</li>
      <li><svg viewBox="0 0 12 12" aria-hidden="true"><path d="M3 0h6v4H3zM1 5h10v6H1zm2 2v1h2V7z"/></svg>555 406 7731</li>
      <li><svg viewBox="0 0 12 12" aria-hidden="true"><path d="M0 2h12v1L6 7 0 3zm0 2.5 6 4 6-4V10H0z"/></svg>ellis@mercerfine.com</li>
    </ul>
    <div class="brand back-brand">
      <span class="brand-mark">RM</span>
      <span class="brand-name">Roland Mercer</span>
      <span class="brand-sub">Jewellery</span>
    </div>
    <div class="divider"></div>
    <div class="address">
      <p>214 Harbor View Road</p>
      <p>Juneau, Alaska 99801</p>
      <p class="web">www.mercerfine.com</p>
    </div>
  </section>
</main>
</body>
</html>
```